RW Holloway LLC Business Card - Civil Engineering & Consulting Firm

We need a Business Card that is elegant, and masculine.  It is our Professional Civil Engineering & Consulting Company located in San Antonio TX (Not s construction or builder firm- no gears & no tool images please). We provide civil engineering services including  commercial site plans, grading and drainage plans, utility plans, hydraulics and hydrology, land planning, utility coordination, and other general civil engineering services related to commercial and residential development.
We have 2 existing Logos. We would like to convey reliability, strength, trustworthiness and attention to detail.  Blues and orange tones as per logo We are OK with the use of a darker blue in the mix.  We have 2 logo versions - Full Company Name Logo to go on the back of card, & Small Icon Logo for the front w/ personal Info.

Target Market(s)
Architects, Real Estate Developers, Other Strctural Engineers, Surveyers, General Contractors
Industry/Entity Type
Professional Civil Engineering
Contact Information for Business Card
Name, Position, Address, Cell & Office #, email, and company website
Font styles to use
Other font styles liked:
- Avian
Requirements
Should not have
- No Tools, No Gears, no Cranes, or Construction Equipment.

```html
<!DOCTYPE html>
<html lang="en">
<head>
<meta charset="utf-8">
<title>RW Holloway LLC — Business Card</title>
<link href="https://fonts.googleapis.com/css2?family=Montserrat:wght@400;500;700&display=swap" rel="stylesheet">
<style>
  :root {
    --stage: #1e1e1e;
    --sky: #7aaad6;
    --dusk: #a7a3a6;
    --amber: #e2913d;
    --orange: #ef8f2a;
    --blue: #7fb0dc;
    --paper: #f1f1f1;
    --paper-shade: #e2e2e2;
    --ink: #222222;
    --white: #ffffff;
  }
  * { box-sizing: border-box; margin: 0; padding: 0; }
  html, body {
    width: 1200px; height: 900px; overflow: hidden;
    background: var(--stage);
    font-family: "Montserrat", sans-serif;
  }
  .card {
    position: absolute; left: 280px; width: 640px; height: 366px;
    box-shadow: 0 10px 30px rgba(0,0,0,.55);
  }
  /* Company side */
  .card--brand {
    top: 48px;
    background: linear-gradient(180deg, var(--sky) 0%, var(--dusk) 45%, var(--amber) 100%);
    color: var(--white);
  }
  .brand-lockup {
    position: absolute; left: 0; right: 0; top: 118px;
    text-align: center;
  }
  .brand-name {
    font-size: 50px; font-weight: 400; letter-spacing: 4px; line-height: 1;
  }
  .brand-rule {
    width: 400px; height: 2px; background: var(--white);
    margin: 18px auto 12px;
  }
  .brand-tagline {
    font-size: 15px; font-weight: 400; letter-spacing: 9px;
  }
  /* Contact side */
  .card--contact {
    top: 470px;
    background: linear-gradient(160deg, var(--paper-shade) 0%, var(--paper) 45%, #f7f7f7 60%, var(--paper-shade) 100%);
    color: var(--ink);
  }
  .person {
    position: absolute; left: 44px; top: 120px; text-align: center; width: 200px;
  }
  .person-name {
    color: var(--orange); font-weight: 700; font-size: 21px; letter-spacing: 1px;
  }
  .person-role {
    font-size: 15px; font-weight: 500; margin-top: 6px;
  }
  .mark {
    position: absolute; left: 262px; top: 70px; width: 92px; height: 240px;
    display: flex; flex-direction: column; align-items: center; justify-content: center; gap: 10px;
  }
  .mark-square { width: 22px; height: 22px; background: var(--blue); }
  .mark-name {
    color: var(--orange); font-weight: 700; font-size: 17px; line-height: 1.25; text-align: center;
  }
  .details {
    position: absolute; left: 382px; top: 104px; font-size: 15px; font-weight: 500; line-height: 1.35;
  }
  .address { margin-bottom: 18px; }
  .contact-list { list-style: none; }
  .contact-list li { display: flex; align-items: center; gap: 10px; margin-bottom: 4px; }
  .contact-list svg { width: 16px; height: 16px; flex: none; fill: var(--orange); }
</style>
</head>
<body>
  <section class="card card--brand">
    <div class="brand-lockup">
      <div class="brand-name">RW Holloway LLC</div>
      <div class="brand-rule"></div>
      <div class="brand-tagline">CONSULTING ENGINEERS</div>
    </div>
  </section>

  <section class="card card--contact">
    <div class="person">
      <div class="person-name">DALEN WHITCOMBE</div>
      <div class="person-role">Co-Founder</div>
    </div>

    <div class="mark">
      <div class="mark-square"></div>
      <div class="mark-name">RW Holloway LLC</div>
    </div>

    <div class="details">
      <p class="address">4180 N. Cedar Ridge Drive<br>Suite 210 Alamo Hts.</p>
      <ul class="contact-list">
        <li>
          <svg viewBox="0 0 16 16" aria-hidden="true"><path d="M3 1h3l1 4-2 1c1 2 3 4 5 5l1-2 4 1v3c0 1-1 2-2 2C7 15 1 9 1 3c0-1 1-2 2-2z"/></svg>
          210-555-0148
        </li>
        <li>
          <svg viewBox="0 0 16 16" aria-hidden="true"><path d="M2 4c2-2 10-2 12 0v2h-3V5H5v1H2zM4 7h8l2 7H2z"/></svg>
          210-555-0193
        </li>
        <li>
          <svg viewBox="0 0 16 16" aria-hidden="true"><path d="M1 3h14v10H1zM2 4l6 5 6-5v1L8 10 2 5z" fill-rule="evenodd"/></svg>
          info@rwhollowayllc
        </li>
        <li>
          <svg viewBox="0 0 16 16" aria-hidden="true"><circle cx="8" cy="8" r="7"/></svg>
          www.rwhollowayllc.com
        </li>
      </ul>
    </div>
  </section>
</body>
</html>
```